Q&J RESTORATION

I want a brochure similiar to the example i've attached.
My company name is Q&J Restoration. The website is: Q-J-Restoration.example.
The phone number is 919.555.0147.

I don't like the "yellow" being the main color of the example so I'm open to suggestions. I want something CLEAN & Simple, like our logo . This will be a bi fold brochure

```html
<!DOCTYPE html>
<html lang="en">
<head>
<meta charset="utf-8">
<title>Q&amp;J Restoration — Bi-fold Brochure</title>
<link rel="stylesheet" href="https://fonts.googleapis.com/css2?family=Poppins:wght@300;400;500;600;700;800&display=swap">
<style>
  :root {
    --board: #dcdcdc;
    --orange: #f05a2c;
    --orange-soft: #f3825c;
    --ink: #231f20;
    --light: #ececee;
    --white: #ffffff;
    --photo-gray-top: #8a8a8a;
    --photo-gray-low: #3a3a3a;
  }
  html, body {
    margin: 0;
    padding: 0;
    width: 821px;
    height: 1200px;
    overflow: hidden;
    background: var(--board);
  }
  .board {
    display: block;
    width: 821px;
    height: 1200px;
    font-family: "Poppins", sans-serif;
  }
  .brand-name { font-family: "Poppins", sans-serif; font-weight: 500; }
  .side-label { font-weight: 800; font-size: 28px; fill: var(--ink); letter-spacing: 0.5px; }
  .headline { font-weight: 800; fill: var(--white); }
  .headline-dark { font-weight: 800; fill: var(--ink); }
  .accent { fill: var(--orange); }
  .tagline { font-weight: 700; font-size: 20px; fill: var(--orange); }
  .contact { font-weight: 500; font-size: 16px; fill: var(--white); }
  .contact-strong { font-weight: 600; font-size: 15px; fill: var(--white); }
  .subhead { font-weight: 700; font-size: 14px; fill: var(--ink); }
  .step-num { font-weight: 700; font-size: 12px; fill: var(--white); }
  .step-title { font-weight: 700; font-size: 13px; fill: var(--ink); }
  .step-body { font-weight: 400; font-size: 10px; fill: var(--ink); }
  .quote-mark { font-weight: 800; font-size: 130px; fill: var(--orange-soft); }
  .quote-text { font-weight: 700; font-size: 18px; fill: var(--white); }
</style>
</head>
<body>
<svg class="board" viewBox="0 0 1589 2324" xmlns="http://www.w3.org/2000/svg">
  <defs>
    <linearGradient id="plansPhoto" x1="0" y1="0" x2="0" y2="1">
      <stop offset="0" stop-color="var(--photo-gray-top)"/>
      <stop offset="0.55" stop-color="var(--photo-gray-low)"/>
      <stop offset="0.75" stop-color="var(--ink)"/>
      <stop offset="1" stop-color="var(--ink)"/>
    </linearGradient>
    <linearGradient id="ceilingPhoto" x1="0" y1="0" x2="1" y2="1">
      <stop offset="0" stop-color="#d9dcdf"/>
      <stop offset="0.5" stop-color="#a7adb4"/>
      <stop offset="1" stop-color="#6e6258"/>
    </linearGradient>
    <linearGradient id="sitePhoto" x1="0" y1="0" x2="1" y2="1">
      <stop offset="0" stop-color="#9fb3c2"/>
      <stop offset="0.45" stop-color="#e08a3a"/>
      <stop offset="1" stop-color="#d9d9d6"/>
    </linearGradient>
    <linearGradient id="moldPhoto" x1="0" y1="0" x2="1" y2="1">
      <stop offset="0" stop-color="#e0562a"/>
      <stop offset="1" stop-color="#b8401f"/>
    </linearGradient>
  </defs>

  <!-- Brand heading -->
  <text class="brand-name" x="794" y="210" text-anchor="middle" font-size="92" fill="var(--ink)">Q&amp;J Restoration</text>

  <!-- Side labels -->
  <text class="side-label" transform="translate(146 1203) rotate(-90)">FRONT / BACK</text>
  <text class="side-label" transform="translate(146 2136) rotate(-90)">INNER</text>

  <!-- Front / back spread -->
  <g class="spread spread-outer" transform="translate(183 404)">
    <!-- back panel -->
    <rect x="0" y="0" width="612" height="799" fill="var(--ink)"/>
    <rect x="0" y="0" width="612" height="799" fill="url(#plansPhoto)" role="img" aria-label="Photo: hands reviewing building plans with pen and ruler"/>
    <polygon points="0,0 92,0 337,246 0,581" fill="var(--orange)"/>

    <!-- front panel -->
    <rect x="612" y="0" width="613" height="799" fill="var(--light)"/>
    <polygon points="637,0 817,0 1225,408 1225,588" fill="var(--white)"/>
    <polygon points="517,0 637,0 1067,430 699,799 612,799 612,95" fill="var(--orange)"/>
    <polygon points="612,96 947,431 612,766" fill="url(#ceilingPhoto)" role="img" aria-label="Photo: restoration workers repairing a ceiling from a ladder"/>
    <polygon points="699,799 1067,431 1225,586 1225,799" fill="var(--ink)"/>

    <!-- back panel content -->
    <text class="brand-name" x="30" y="262" font-size="28" textLength="250" lengthAdjust="spacingAndGlyphs" fill="var(--white)">Q&amp;J Restoration</text>
    <text class="headline" x="46" y="652" font-size="37">INSURANCE CLAIM ?</text>
    <text class="tagline" x="46" y="678">WE'RE ON YOUR TEAM.</text>

    <g class="contact-row">
      <rect x="46" y="707" width="26" height="26" rx="5" fill="var(--orange)"/>
      <path d="M54 713 l3 0 l1.5 4 l-2 1.5 a9 9 0 0 0 4 4 l1.5 -2 l4 1.5 l0 3 a2 2 0 0 1 -2 1.5 a13 13 0 0 1 -11.5 -11.5 a2 2 0 0 1 1.5 -2 z" fill="var(--white)"/>
      <text class="contact" x="85" y="726">919.555.0147</text>
    </g>
    <g class="contact-row">
      <rect x="46" y="743" width="26" height="26" rx="5" fill="var(--orange)"/>
      <rect x="53" y="751" width="12" height="9" rx="1" fill="var(--white)"/>
      <path d="M53 752 l6 4.5 l6 -4.5" fill="none" stroke="var(--orange)" stroke-width="1.2"/>
      <text class="contact" x="85" y="762">Q-J-Restoration.example</text>
    </g>

    <!-- front panel content -->
    <text class="brand-name" x="1055" y="178" font-size="34" text-anchor="middle" textLength="300" lengthAdjust="spacingAndGlyphs" fill="var(--ink)">Q&amp;J Restoration</text>
    <text class="headline" x="1187" y="648" font-size="42" text-anchor="end">INSURANCE</text>
    <text x="1187" y="687" font-size="42" font-weight="400" text-anchor="end" class="accent">CLAIM</text>
    <text class="headline" x="1187" y="726" font-size="42" text-anchor="end">SPECIALIST</text>
    <g class="web-row">
      <circle cx="968" cy="766" r="7" fill="var(--orange)"/>
      <path d="M961 766 h14 M968 759 v14" stroke="var(--ink)" stroke-width="1"/>
      <text class="contact-strong" x="1187" y="771" text-anchor="end" textLength="205" lengthAdjust="spacingAndGlyphs">Q-J-Restoration.example</text>
    </g>
  </g>

  <!-- Inner spread -->
  <g class="spread spread-inner" transform="translate(183 1337)">
    <!-- left inner panel -->
    <rect x="0" y="0" width="612" height="799" fill="var(--white)"/>
    <polygon points="287,0 612,0 612,578 164,130" fill="url(#sitePhoto)" role="img" aria-label="Photo: smiling site worker in hard hat and safety vest holding plans"/>
    <polygon points="0,0 287,0 84,208 0,125" fill="var(--orange)"/>
    <polygon points="397,799 612,584 612,799" fill="var(--ink)"/>

    <!-- right inner panel -->
    <rect x="612" y="0" width="613" height="799" fill="var(--ink)"/>
    <polygon points="612,0 850,0 1022,172 612,582" fill="var(--light)"/>
    <polygon points="1002,188 1016,174 1225,383 1225,411" fill="var(--white)"/>
    <polygon points="992,208 1225,441 1225,531 667,531" fill="url(#moldPhoto)" role="img" aria-label="Photo: worried homeowner beside a mold-damaged wall"/>

    <!-- left inner content -->
    <text class="headline-dark" x="44" y="320" font-size="33">WATER OR</text>
    <text class="headline-dark" x="44" y="353" font-size="33">MOLD DAMAGE?</text>
    <text class="subhead" x="44" y="381">WHAT HAPPENS AFTER THA CLEANUP</text>

    <g class="step">
      <rect x="44" y="413" width="26" height="26" rx="5" fill="var(--orange)"/>
      <text class="step-num" x="57" y="430" text-anchor="middle">01</text>
      <text class="step-title" x="78" y="431">ADJUSTERS'S INSPECTION</text>
      <text class="step-body" x="43" y="456">
        <tspan x="43" dy="0">Feel Confident. Be sure you - received a fair and  accurate</tspan>
        <tspan x="43" dy="12">assessment &amp; repair of all damages with our teom's Systems of</tspan>
        <tspan x="43" dy="12">industry leading  Estimating Systems and On-Site Review.</tspan>
      </text>
    </g>
    <g class="step">
      <rect x="44" y="503" width="26" height="26" rx="5" fill="var(--orange)"/>
      <text class="step-num" x="57" y="520" text-anchor="middle">02</text>
      <text class="step-title" x="78" y="521">UNDER ONE ROOF</text>
      <text class="step-body" x="43" y="546">
        <tspan x="43" dy="0">Don't Worry. You won't need to arrange  meetings will, multiple</tspan>
        <tspan x="43" dy="12">contractors; we take care of everything from demo to final</tspan>
        <tspan x="43" dy="12">cleanup.</tspan>
      </text>
    </g>
    <g class="step">
      <rect x="44" y="592" width="26" height="26" rx="5" fill="var(--orange)"/>
      <text class="step-num" x="57" y="609" text-anchor="middle">03</text>
      <text class="step-title" x="78" y="610">TIMELY SETTELMENT</text>
      <text class="step-body" x="43" y="635">
        <tspan x="43" dy="0">Don't wait. Minimize the hassle of long  processing times From</tspan>
        <tspan x="43" dy="12">Estimote to Settlement when you team up with on Insurance</tspan>
        <tspan x="43" dy="12">Repair Specialist.</tspan>
      </text>
    </g>
    <g class="step">
      <rect x="44" y="683" width="26" height="26" rx="5" fill="var(--orange)"/>
      <text class="step-num" x="57" y="700" text-anchor="middle">04</text>
      <text class="step-title" x="78" y="701">SUPERIOR CRAFTSMANSHIP</text>
      <text class="step-body" x="43" y="726">
        <tspan x="43" dy="0">Don't settle for satisfactory. Our team is committed to the highest</tspan>
        <tspan x="43" dy="12">standards of excellence every step of the way. Trust us when we</tspan>
        <tspan x="43" dy="12">say that well make you smile.</tspan>
      </text>
    </g>

    <!-- right inner content -->
    <text class="headline-dark" x="647" y="161" font-size="54">BUILD</text>
    <text x="647" y="215" font-size="54" font-weight="800" class="accent">RENOVATE</text>
    <text class="headline-dark" x="647" y="269" font-size="54">RESTORE</text>

    <text class="quote-mark" x="812" y="505">“</text>
    <text class="quote-text" x="850" y="473" textLength="236" lengthAdjust="spacingAndGlyphs">BEING A GOOD EXAMPLE</text>
    <text class="quote-text" x="850" y="495" textLength="287" lengthAdjust="spacingAndGlyphs">IS THE BEST FORM OF SERVICE</text>

    <text class="brand-name" x="937" y="690" font-size="52" fill="var(--white)" text-anchor="middle" textLength="420" lengthAdjust="spacingAndGlyphs">Q&amp;J Restoration</text>
  </g>
</svg>
</body>
</html>
```